web page design with coding

We are a start up insurance agency who needs to design a full functional web page. we recently did a postcard design though drawkettle I will upload the final project for you to see the color scheme/font we would like to continue to use. I also have a rough draft of verbage I would like our website to have. I will upload that as well.

Reason: I am sorry but the person who will make the final decision on the website is out of the country at the moment and will make the final decision when he returns.

Industry/Entity Type

Insurance

Coding

Coded - Design and coding required

```html
<!DOCTYPE html>
<html lang="en">
<head>
<meta charset="utf-8">
<title>Meridian Assurance Group</title>
<link href="https://fonts.googleapis.com/css2?family=Open+Sans:ital,wght@0,400;0,600;0,700;1,400&family=Oswald:wght@300;400&display=swap" rel="stylesheet">
<style>
:root{
  --navy:#1b3c6c;
  --navy-dark:#15305a;
  --nav-top:#27569a;
  --nav-bottom:#1a3d70;
  --green:#3b8c40;
  --green-dark:#2f7434;
  --text:#555;
  --muted:#888;
  --line:#dcdcdc;
  --footer:#161616;
  --footer-text:#b9b9b9;
  --white:#fff;
}
*{box-sizing:border-box;margin:0;padding:0}
html,body{width:1200px;height:2731px;overflow:hidden}
body{font-family:"Open Sans",Arial,sans-serif;color:var(--text);background:var(--white);position:relative}
.wrap{position:relative;width:1200px}

/* header */
.site-header{height:133px;position:relative}
.brand{position:absolute;left:100px;top:22px;width:146px;height:91px;border:2px solid #444;display:flex;align-items:center;justify-content:center;font-weight:700;font-size:38px;color:#333;letter-spacing:1px}
.contact-bar{position:absolute;right:98px;top:46px;display:flex;align-items:center;gap:34px;font-size:14px;color:#666}
.contact-item{display:flex;align-items:center;gap:8px}
.contact-item b{color:var(--green);font-weight:700;font-size:15px}
.btn-quote{background:var(--green);color:#fff;font-weight:700;font-size:15px;padding:11px 30px;border-radius:2px}

/* nav */
.main-nav{height:57px;background:linear-gradient(var(--nav-top),var(--nav-bottom));display:flex;padding-left:100px}
.main-nav a{display:block;height:57px;line-height:57px;color:#fff;font-size:12px;text-decoration:none;text-align:center;text-transform:uppercase}
.main-nav a.active{background:var(--green)}

/* hero */
.hero{height:551px;position:relative;background:linear-gradient(120deg,#6d7a3e 0%,#51622e 40%,#86874a 70%,#5b6d30 100%);overflow:hidden}
.hero-photo{position:absolute;inset:0}
.hero-arrow{position:absolute;top:248px;width:42px;height:42px;border:2px solid rgba(255,255,255,.55);border-radius:50%}
.hero-title{position:absolute;left:100px;top:530px;font-family:"Oswald","Arial Narrow",sans-serif;font-weight:300;font-size:66px;color:#fff;line-height:1;top:340px}
.hero-sub{position:absolute;left:100px;top:420px;width:440px;font-weight:700;font-size:15px;line-height:22px;color:#fff;text-transform:uppercase}
.quote-form{position:absolute;left:810px;top:45px;width:292px;height:461px;background:#fff;box-shadow:0 2px 6px rgba(0,0,0,.3)}
.quote-form h3{height:50px;line-height:50px;background:var(--navy);color:#fff;text-align:center;font-size:16px;font-weight:700}
.form-body{padding:16px 24px}
.secure{color:var(--green);font-size:12px;margin-bottom:14px;display:flex;align-items:center;gap:6px}
.field-label{font-size:12px;color:#444;font-weight:600;margin-bottom:6px}
.field{height:30px;background:#f4f4f4;border:1px solid #eee;margin-bottom:18px}
.checks{display:grid;grid-template-columns:1fr 1fr;row-gap:14px;font-size:12px;color:#666;margin:8px 0 24px}
.checks span{display:flex;align-items:center;gap:10px}
.checks i{width:14px;height:14px;border:1px solid #bbb;display:inline-block}
.btn-step{height:38px;line-height:38px;background:var(--green);color:#fff;text-align:center;font-size:12px;font-weight:700;border-radius:2px}

/* welcome */
.welcome{height:588px;padding-top:34px;text-align:center}
.section-title{font-size:25px;font-weight:700;color:var(--navy);letter-spacing:.5px}
.welcome p{width:1000px;margin:14px auto 0;font-size:11.5px;line-height:22px;color:#666}
.services{position:absolute;left:100px;top:240px;width:1002px;height:303px;border:1px solid var(--line);display:flex}
.service{flex:1;text-align:center;padding-top:30px}
.service + .service{border-left:1px solid var(--line)}
.service h4{font-size:15px;font-weight:700;color:var(--navy);margin-top:18px}
.service p{width:400px;margin:14px auto 0;font-size:11.5px;line-height:22px;color:#777}
.btn-green{display:inline-block;background:var(--green);color:#fff;font-size:11.5px;font-weight:700;padding:12px 20px;margin-top:20px;border-radius:2px}

/* about */
.about{height:350px;background:linear-gradient(90deg,#1a3b6b,#23487e 60%,#1c3c6c);position:relative;color:#fff}
.about h2{position:absolute;left:100px;top:42px;font-size:26px;font-weight:700}
.about-text{position:absolute;left:100px;top:95px;width:560px;font-size:12px;line-height:22px}
.about-text p+p{margin-top:12px}
.about .btn-green{position:absolute;left:100px;top:260px;margin:0;padding:13px 26px}
.about-photo{position:absolute;left:701px;top:51px;width:401px;height:246px;border:4px solid #fff;background:linear-gradient(135deg,#7aa05a,#c9a98a 55%,#5d7b3e)}

/* agents */
.agents{height:506px;position:relative;text-align:center;padding-top:34px}
.agents .lead{width:760px;margin:10px auto 0;font-size:13.5px;line-height:22px;color:#888}
.agent-photo{position:absolute;left:100px;top:133px;width:250px;height:373px;background:linear-gradient(#f5f5f5,#ddd 30%,#2a2c36 45%,#1c1e27)}
.agent-info{position:absolute;left:415px;top:143px;width:687px;text-align:left;font-size:11.5px;color:#666}
.agent-meta{padding-bottom:14px;border-bottom:1px solid var(--line)}
.agent-meta b{color:var(--green);font-weight:400}
.agent-bio{margin-top:12px;line-height:22px}
.agent-bio strong{color:var(--green)}
.agent-bio p+p{margin-top:12px}

/* mission */
.mission{height:252px;background:linear-gradient(90deg,#2f7b3a,#3a8d44 50%,#2f7b3a);position:relative}
.mission-box{position:absolute;left:275px;top:60px;width:650px;height:130px;background:#fff;text-align:center;padding-top:20px}
.mission-box h3{font-size:21px;font-weight:600;color:var(--navy)}
.mission-box p{width:560px;margin:10px auto 0;font-size:11.5px;line-height:22px;font-style:italic;color:#666}

/* footer */
.site-footer{height:294px;background:var(--footer);position:relative;color:var(--footer-text)}
.f-col{position:absolute;top:36px;font-size:11.5px}
.f-col h5{color:#fff;font-size:15px;font-weight:700;margin-bottom:14px}
.f-col li{list-style:none;line-height:22px}
.f-col li::before{content:"›";margin-right:8px;color:#888}
.nl-field{width:222px;height:32px;background:#2c2c2c;color:#999;font-size:11px;padding:8px 14px;margin-bottom:10px}
.btn-sub{width:100px;height:36px;line-height:36px;text-align:center;background:var(--navy);color:#fff;font-size:10.5px;font-weight:700}
.f-contact div{display:flex;gap:12px;align-items:flex-start;margin-bottom:14px;line-height:18px}
.f-bottom{position:absolute;left:100px;right:98px;top:231px;border-top:1px solid #2c2c2c;padding-top:18px;display:flex;justify-content:space-between;align-items:center;font-size:11px;color:#ccc}
.social{display:flex;gap:8px;align-items:center}
.social i{width:26px;height:26px;border-radius:50%;display:inline-block}
</style>
</head>
<body>
<div class="wrap">

<header class="site-header">
  <div class="brand">MAG</div>
  <div class="contact-bar">
    <span class="contact-item">
      <svg width="14" height="22" viewBox="0 0 14 22"><rect x="1" y="1" width="12" height="20" rx="2" fill="none" stroke="#888" stroke-width="1.5"/><circle cx="7" cy="17.5" r="1" fill="#888"/></svg>
      Call Us: <b>(305) 555-0147</b>
    </span>
    <span class="contact-item">
      <svg width="22" height="18" viewBox="0 0 22 18"><rect x="1" y="3" width="20" height="14" fill="none" stroke="#888" stroke-width="1.5"/><path d="M1 3l10 8 10-8" fill="none" stroke="#888" stroke-width="1.5"/></svg>
      Mail Us: <b>info@meridian-ag.com</b>
    </span>
    <span class="btn-quote">Get a Quote ▾</span>
  </div>
</header>

<nav class="main-nav">
  <a class="active" style="width:135px">Home</a>
  <a style="width:145px">About Us</a>
  <a style="width:150px">Services</a>
  <a style="width:150px">Insurance</a>
  <a style="width:140px">Agents</a>
  <a style="width:165px">Our Mission</a>
  <a style="width:117px">Contact Us</a>
</nav>

<section class="hero">
  <div class="hero-photo" role="img" aria-label="Photo of a young family walking outdoors through green grass, parents carrying two small children"></div>
  <span class="hero-arrow" style="left:42px"><svg width="38" height="38" viewBox="0 0 38 38"><path d="M22 12l-7 7 7 7" fill="none" stroke="#fff" stroke-width="2"/></svg></span>
  <span class="hero-arrow" style="left:1118px"><svg width="38" height="38" viewBox="0 0 38 38"><path d="M16 12l7 7-7 7" fill="none" stroke="#fff" stroke-width="2"/></svg></span>
  <h1 class="hero-title">WE WORK FOR YOU!</h1>
  <p class="hero-sub">Meridians can help ensure you have the coverage you need to protect your family's assets if the unexpected happens...</p>
  <form class="quote-form">
    <h3>INSURANCE QUATE</h3>
    <div class="form-body">
      <div class="secure"><svg width="10" height="12" viewBox="0 0 10 12"><rect x="0" y="5" width="10" height="7" fill="#3b8c40"/><path d="M2 5V3a3 3 0 016 0v2" fill="none" stroke="#3b8c40" stroke-width="1.5"/></svg>Secure 256 bit SSL Encryption</div>
      <div class="field-label">Name*</div><div class="field"></div>
      <div class="field-label">E-mail*</div><div class="field"></div>
      <div class="field-label">Phone*</div><div class="field"></div>
      <div class="field-label">Select Type of Insurance*</div>
      <div class="checks">
        <span><i></i>Personal</span><span><i></i>Business</span>
        <span><i></i>Life / Health</span><span><i></i>Benefits</span>
      </div>
      <div class="btn-step">GO TO STEP 2</div>
    </div>
  </form>
</section>

<section class="welcome wrap">
  <h2 class="section-title">WELCOME TO MAG</h2>
  <p>Meridian Assurance Group has joined with regional &amp; national insurance companies to provide quality products and superior service. We take the time to discuss options and coverages, not to just sell insurance products. We strive to educate you in the decision making process to become an informed consumer...</p>
  <p>We specialize in commercial business &amp; personal insurance. We are committed to providing personal attention to all your insurance needs. At Meridian Assurance Group, we are independent insurance agents. As independent agents, we do not work for any one insurance company; we sell coverage from several different companies. This allows us to focus on providing you with the right amount of insurance and the right type of coverage for your unique needs...</p>
  <div class="services">
    <div class="service">
      <svg width="90" height="64" viewBox="0 0 90 64" fill="#1b3c6c"><circle cx="35" cy="12" r="7"/><circle cx="55" cy="14" r="6"/><path d="M27 22h16v22H27zM48 24h14v18H48z"/><path d="M4 20c4 14 14 30 34 38h-8C14 54 4 40 2 22zM86 20c-4 14-14 30-34 38h8c16-4 26-18 28-36z"/></svg>
      <h4>PERSONAL INSURANCE</h4>
      <p>Sed ut perspiciatis unde omnis iste natus error sit voluptatem doloremque lium, totam rem aperiam, eaque ipsa quae ab illo inventore veritatis et quasi ecto beatae vitae dicta sunt explicabo. Nemo enim ipsam...</p>
      <span class="btn-green">CLICK VIEW MORE INFO</span>
    </div>
    <div class="service">
      <svg width="90" height="64" viewBox="0 0 90 64" fill="#1b3c6c"><path d="M8 34l18-18 8 8-18 18zM58 10l16 16-6 6-16-16z"/><path d="M28 30l14-14h12l16 16-18 18c-3 3-7 3-10 0z"/></svg>
      <h4>BUSINESS INSURANCE</h4>
      <p>Sed ut perspiciatis unde omnis iste natus error sit voluptatem doloremque lium, totam rem aperiam, eaque ipsa quae ab illo inventore veritatis et quasi ecto beatae vitae dicta sunt explicabo. Nemo enim ipsam...</p>
      <span class="btn-green">CLICK VIEW MORE INFO</span>
    </div>
  </div>
</section>

<section class="about">
  <h2>ABOUT MAG</h2>
  <div class="about-text">
    <p>Established in 2015, Meridian Assurance Group is a full service independent insurance agency. Our licensed agents have the experience to custom tailor a program to meet your specific needs &amp; our professional support staff will provide you with top notch customer service to help ease the burden of managing your insurance program...</p>
    <p>We have established relationships with carriers in order to offer you the most competitive products and services available in the marketplace today. We look forward to working with you!</p>
  </div>
  <span class="btn-green">READ MORE</span>
  <div class="about-photo" role="img" aria-label="Photo of a smiling family of four outdoors"></div>
</section>

<section class="agents">
  <h2 class="section-title">AGENTS</h2>
  <p class="lead">Sed ut perspiciatis unde omnis iste natus error sit voluptatem accusantium doloremque laudantium, totam rem aperiam, eaque ipsa quae ab illo inventore veritatis et quasi architecto beatae vitae dicta sunt</p>
  <div class="agent-photo" role="img" aria-label="Portrait photo of an agent in a dark suit"></div>
  <div class="agent-info">
    <div class="agent-meta">AGENT NAME: <b>DANIEL</b> &nbsp;–&nbsp; EDUCATION: <b>REM APERIAM</b> &nbsp;–&nbsp; INSURANCE EXPERIENCE: <b>5 YEARS</b> &nbsp;–&nbsp; PROFESSIONAL MEMBERSHIPS: <b>YES</b></div>
    <div class="agent-bio">
      <p><strong>➔ DANIEL'S BIO :</strong> Sed ut perspiciatis unde omnis iste natus error sit voluptatem accusantium doloremque laudantium, totam rem aperiam, eaque ipsa quae ab illo inventore veritatis et quasi architecto beatae vitae dicta sunt explicabo. Nemo enim ipsam voluptatem quia voluptas sit aspernatur aut odit aut fugit, sed quia consequuntur magni dolores eos qui ratione voluptatem sequi nesciunt. Neque porro quisquam est, qui dolorem ipsum quia dolor sit amet, consectetur, adipisci velit, sed quia non numquam eius modi tempora incidunt ut labore et dolore magnam aliquam quaerat voluptatem...</p>
      <p>sed quia non numquam eius modi tempora incidunt ut labore et dolore magnam aliquam quaerat voluptatem. Ut enim ad minima veniam, quis nostrum exercitationem ullam corporis suscipit laboriosam, nisi ut aliquid ex ea commodi consequatur? Quis autem quia voluptas sit aspernatur aut odit aut fugit, sed quia consequuntur magni dolores eos qui ratione voluptatem sequi nesciunt vel eum iure reprehenderit qui in ea voluptate velit esse...</p>
    </div>
  </div>
</section>

<section class="mission">
  <div class="mission-box">
    <h3>Meridian Assurance Group Mission Statement</h3>
    <p>Meridian Assurance Group is committed to providing the best risk management solutions to fit each client's unique needs. This includes providing creative solutions as if we were seeking insurance for our own family.</p>
  </div>
</section>

<footer class="site-footer">
  <div class="f-col" style="left:100px"><h5>HOME</h5><ul><li>About us</li><li>Services</li><li>Insurance</li><li>Agents</li><li>Our Mission</li><li>Contact Us</li></ul></div>
  <div class="f-col" style="left:242px"><h5>INSURANCE</h5><ul><li>Auto Insurance</li><li>Home Insurance</li><li>Business Insurance</li><li>Life Insurance</li><li>Other Insurance</li><li>Personal Insurance</li></ul></div>
  <div class="f-col" style="left:433px"><h5>ADDITIONAL LINKS</h5><ul><li>Our Company</li><li>Our Team</li><li>Our Partners</li><li>Careers</li><li>Contact Us</li></ul></div>
  <div class="f-col" style="left:643px"><h5>NEWS LETTER</h5><div class="nl-field">Name</div><div class="nl-field">E-mail</div><div class="btn-sub">SUBSCRIBE</div></div>
  <div class="f-col f-contact" style="left:934px"><h5>CONTACT</h5>
    <div><svg width="14" height="20" viewBox="0 0 14 20"><path d="M7 1a6 6 0 016 6c0 5-6 12-6 12S1 12 1 7a6 6 0 016-6z" fill="none" stroke="#999" stroke-width="1.5"/><circle cx="7" cy="7" r="2" fill="#999"/></svg><span>1820 Harbor Lane Suite 140<br>Miami, FL 33101</span></div>
    <div><svg width="14" height="20" viewBox="0 0 14 20"><rect x="1" y="1" width="12" height="18" rx="2" fill="none" stroke="#999" stroke-width="1.5"/></svg><span>(305) 555-0147</span></div>
    <div><svg width="16" height="14" viewBox="0 0 16 14"><rect x="1" y="1" width="14" height="12" fill="none" stroke="#999" stroke-width="1.5"/><path d="M1 1l7 6 7-6" fill="none" stroke="#999" stroke-width="1.5"/></svg><span>info@meridian-ag.com</span></div>
  </div>
  <div class="f-bottom">
    <span>COPYRIGHTS©MERIDIAN-AG . 2016 | ALLRIGHTS RESERVED.</span>
    <span class="social">CONNECT WITH US: <i style="background:#3b5b9c"></i><i style="background:#2aa3e0"></i><i style="background:#d8432f"></i><i style="background:#1d74b0"></i><i style="background:#cc2127"></i></span>
  </div>
</footer>

</div>
</body>
</html>
```